OBK Farcoast Logistics Limited

We need the buissnes card to be very exclusive. As we are all young in our company. We need this to be the gate to make our clients feel deep interest for us.

We are focused in as International Trade advisors, and our products go from Oil Tanker Ships to Rubber balls for dogs.

Our Slogan is Bringing Far Near.
And our main marketing will be through Internet.

We were stablished in 2009 In Mexico and we also have offices in Hong Kong.
We have representatives in China and Europe.

Target Market(s)

Is every company or Individual that wants to develop an International Project or product development or Logistic service of Goods and people.
Some of our current projects are Ship Brokerage, Mine Brokerage, Real State and Product Pormotional development.

Industry/Entity Type

It Company

Requirements
Must have
• Our Logo and slogan, and make the card accoriding to the logo.
Nice to have
• Our Colors

```html
<!DOCTYPE html>
<html lang="en">
<head>
<meta charset="utf-8">
<title>Business Card</title>
<link rel="stylesheet" href="https://fonts.googleapis.com/css2?family=Open+Sans:wght@400;600;700&display=swap">
<style>
  :root {
    --page-bg: #e9eaee;
    --card-white: #ffffff;
    --brand-blue: #1b7fb6;
    --brand-green: #8cc63f;
    --text-grey: #4a4a4a;
    --card-shadow: 0 14px 30px rgba(40, 50, 70, 0.22);
  }
  * { box-sizing: border-box; margin: 0; padding: 0; }
  html, body { width: 1200px; height: 987px; overflow: hidden; }
  body {
    background: var(--page-bg);
    font-family: "Open Sans", Arial, sans-serif;
    display: flex;
    flex-direction: column;
    align-items: center;
    justify-content: center;
    gap: 44px;
  }
  .card {
    position: relative;
    width: 760px;
    height: 434px;
    border-radius: 30px;
    box-shadow: var(--card-shadow);
    overflow: hidden;
  }

  /* Front */
  .card-front { background: var(--card-white); color: var(--text-grey); }
  .accent-bar {
    position: absolute; left: 0; top: 40px;
    width: 12px; height: 62px; background: var(--brand-blue);
  }
  .identity { position: absolute; left: 62px; top: 40px; }
  .identity .name { color: var(--brand-blue); font-weight: 700; font-size: 28px; line-height: 1.1; }
  .identity .position { color: var(--brand-green); font-size: 19px; line-height: 1.2; }
  .address { position: absolute; left: 62px; top: 128px; font-size: 19px; line-height: 1.4; }
  .contacts { position: absolute; left: 62px; top: 212px; list-style: none; font-size: 19px; line-height: 1.55; }
  .contacts li { display: flex; align-items: center; gap: 12px; }
  .contacts svg { width: 18px; height: 18px; fill: var(--brand-blue); }
  .website { position: absolute; left: 62px; bottom: 42px; font-size: 21px; letter-spacing: 2px; }
  .website .domain { color: var(--brand-blue); }

  .brand-block {
    position: absolute; right: 90px; bottom: 70px;
    display: flex; flex-direction: column; align-items: center;
  }
  .brand-row { display: flex; align-items: center; gap: 16px; }
  .brand-dot { width: 46px; height: 46px; border-radius: 50%; background: var(--brand-blue); }
  .brand-name { color: var(--brand-green); font-weight: 700; font-size: 104px; line-height: 1; letter-spacing: 4px; }
  .slogan { color: var(--brand-blue); font-size: 22px; margin-top: 6px; }

  /* Back */
  .card-back {
    background: var(--brand-blue);
    color: #fff;
    display: flex; flex-direction: column; align-items: center; justify-content: center;
  }
  .card-back .brand-name { color: #fff; font-size: 150px; letter-spacing: 8px; }
  .card-back .slogan { color: #fff; font-size: 30px; margin-top: 4px; }
  .card-back .web { font-size: 22px; letter-spacing: 6px; margin-top: 34px; }
</style>
</head>
<body>
  <section class="card card-front">
    <span class="accent-bar"></span>
    <div class="identity">
      <p class="name">Your Name</p>
      <p class="position">Position</p>
    </div>
    <p class="address">00, Complex Name<br>City, State, 00045</p>
    <ul class="contacts">
      <li><svg viewBox="0 0 24 24" aria-hidden="true"><path d="M6.6 10.8a15 15 0 0 0 6.6 6.6l2.2-2.2a1 1 0 0 1 1-.25 11.4 11.4 0 0 0 3.6.57 1 1 0 0 1 1 1V20a1 1 0 0 1-1 1A17 17 0 0 1 3 4a1 1 0 0 1 1-1h3.5a1 1 0 0 1 1 1c0 1.25.2 2.45.57 3.57a1 1 0 0 1-.25 1z"/></svg>123-456-7890</li>
      <li><svg viewBox="0 0 24 24" aria-hidden="true"><path d="M8 1h8a2 2 0 0 1 2 2v18a2 2 0 0 1-2 2H8a2 2 0 0 1-2-2V3a2 2 0 0 1 2-2zm0 3v13h8V4zm4 15a1.2 1.2 0 1 0 0 2.4A1.2 1.2 0 0 0 12 19z"/></svg>123-456-7890</li>
      <li><svg viewBox="0 0 24 24" aria-hidden="true"><path d="M2 5h20v14H2zm2 2v.5l8 5 8-5V7zm0 2.8V17h16V9.8l-8 5z"/></svg>info@farcoast.com</li>
    </ul>
    <p class="website">www.<span class="domain">farcoast</span>.com</p>
    <div class="brand-block">
      <div class="brand-row">
        <span class="brand-dot"></span>
        <span class="brand-name">OBK</span>
      </div>
      <p class="slogan">Bringing Far Near</p>
    </div>
  </section>

  <section class="card card-back">
    <span class="brand-name">OBK</span>
    <p class="slogan">Bringing Far Near</p>
    <p class="web">www.farcoast.com</p>
  </section>
</body>
</html>
```